Real Estate Company / Capital Needs Cards!

need business cards designed using the logos that were just designed by pixelbarn.

Reason: per designers request deadline extended 1 day…thank you.

Target Market(s)

Investors and clients looking to purchase real estate or invest in the business.

Industry/Entity Type

Business

Requirements
Must have
• two designs - one for the real estate logo and one for the capital logo, similar but slightly different.
Nice to have
• something to make it pop (perhaps on the back)
Should not have
• much color

```html
<!DOCTYPE html>
<html lang="en">
<head>
<meta charset="utf-8">
<title>Morrow Real Estate – Business Cards</title>
<link rel="stylesheet" href="https://fonts.googleapis.com/css2?family=Cinzel:wght@400;600&family=Open+Sans:wght@600&display=swap">
<style>
  :root {
    --backdrop: #e9e6e2;
    --card-dark: #26282c;
    --card-mid: #34363b;
    --silver: #e4e4e4;
    --silver-soft: #c9c9c9;
    --mark-faint: rgba(255, 255, 255, 0.07);
  }
  html, body {
    margin: 0;
    padding: 0;
    overflow: hidden;
  }
  .canvas {
    width: 1200px;
    height: 498px;
    background: var(--backdrop);
    position: relative;
    overflow: hidden;
  }
  .card {
    position: absolute;
    top: 79px;
    width: 540px;
    height: 340px;
    background: radial-gradient(ellipse at 40% 35%, var(--card-mid), var(--card-dark) 75%);
    box-shadow: 0 6px 18px rgba(0, 0, 0, 0.25);
    overflow: hidden;
    color: var(--silver);
    font-family: "Cinzel", serif;
  }
  .card--front { left: 30px; }
  .card--back { left: 630px; }

  /* Front */
  .brand {
    position: absolute;
    left: 36px;
    top: 36px;
    display: flex;
    align-items: center;
    gap: 14px;
  }
  .brand-square {
    width: 62px;
    height: 62px;
    background: var(--silver);
    border-radius: 4px;
  }
  .brand-name {
    font-weight: 400;
    color: var(--silver);
    line-height: 1;
  }
  .brand-name .line-main { display: block; font-size: 40px; letter-spacing: 1px; }
  .brand-name .line-sub { display: block; font-size: 17px; letter-spacing: 3px; margin-top: 4px; }

  .faint-square {
    position: absolute;
    background: var(--mark-faint);
    border-radius: 10px;
  }
  .card--front .faint-square { left: 390px; top: 130px; width: 130px; height: 150px; }

  .contact {
    position: absolute;
    left: 40px;
    top: 206px;
    font-size: 15px;
    line-height: 1.35;
    color: var(--silver-soft);
  }
  .contact .person { font-size: 18px; color: var(--silver); margin-bottom: 4px; }
  .contact .address { margin-top: 8px; font-size: 15px; letter-spacing: 1px; }

  /* Back */
  .card--back .faint-square { left: 200px; top: 55px; width: 150px; height: 180px; }
  .back-brand {
    position: absolute;
    left: 0;
    right: 0;
    top: 110px;
    text-align: center;
    font-weight: 400;
    line-height: 1;
  }
  .back-brand .line-main { display: block; font-size: 72px; letter-spacing: 2px; }
  .back-brand .line-sub { display: block; font-size: 30px; letter-spacing: 6px; margin-top: 4px; }
  .website {
    position: absolute;
    left: 0;
    right: 0;
    top: 268px;
    text-align: center;
    font-family: "Open Sans", sans-serif;
    font-weight: 600;
    font-size: 15px;
    letter-spacing: 3px;
    color: var(--silver);
  }
</style>
</head>
<body>
<main class="canvas">
  <section class="card card--front" aria-label="Card front">
    <div class="faint-square"></div>
    <div class="brand">
      <span class="brand-square"></span>
      <span class="brand-name">
        <span class="line-main">MORROW</span>
        <span class="line-sub">REAL ESTATE</span>
      </span>
    </div>
    <div class="contact">
      <div class="person">Your Name, Title</div>
      <div>P: 123-456-7980</div>
      <div>F: 123-568-7896</div>
      <div>E: Morrowrealestate@mail.com</div>
      <div class="address">Street Name City Name State ZipCode</div>
    </div>
  </section>

  <section class="card card--back" aria-label="Card back">
    <div class="faint-square"></div>
    <div class="back-brand">
      <span class="line-main">MORROW</span>
      <span class="line-sub">REAL ESTATE</span>
    </div>
    <div class="website">www.morrowrealestate.com</div>
  </section>
</main>
</body>
</html>
```